Halvik - consultancy website

I need a new design for my webpage/presence [to be functioning with Wordpress - I have a programmer to set it up but not the design idea].
My company is Halvik - a consultancy firm focused on growth management for Swedish SME's primarily;. We call it Leadership toolkit for firms on the rise, kind of a doctor helping small become big. Contentwise, its a simple frontpage + 3-4 subpages with content re company/myself/focus etc. The new site should communicate a fresh, trustworthy take yet simple and functional on all devices [i.e. think UI compatible for mobile/tablet]. Current building parts/form elements are
a) existing logo and text elements
b) existing pictures
c) the yellowish color
colours and new ideas on pictures/positioning are welcome. I prefer a 'full width page' solution with centralised text elements but that's all up to you to suggest. Current site is a quickfix made by myself - now I'm moving it to a new platform so want to take the opportunity to make it
Nothing superspecial as it is a 2-man show; on the other hand I still want to have a modern & fresh reflection of my brand in digital environments. Help me out!
www.halvik-demo.se
Best
Lina Bergqvist

```html
<!DOCTYPE html>
<html lang="en">
<head>
<meta charset="utf-8">
<title>Halvik – Services</title>
<link href="https://fonts.googleapis.com/css2?family=Arimo:wght@400;700&family=PT+Serif:wght@400&display=swap" rel="stylesheet">
<style>
:root{
  --accent:#e8992f;
  --ink:#222;
  --text:#666;
  --line:#ddd;
  --bar:#2b2b2b;
  --band:#353535;
  --footer:#1c1c1c;
  --bottom:#0e0e0e;
  --social-a:#3b5a9a;
  --social-b:#3aa8e0;
  --social-c:#dd4b39;
}
*{margin:0;padding:0;box-sizing:border-box}
html,body{width:782px;height:1200px;overflow:hidden;background:#fff}
body{position:relative;font-family:"Arimo",Arial,sans-serif;color:var(--ink)}
.abs{position:absolute}

.header{position:absolute;left:0;top:0;width:782px;height:86px;background:#fff}
.brand{left:64px;top:16px;font-family:"PT Serif",Georgia,serif;font-size:33px;color:var(--ink);line-height:1}
.tagline{left:66px;top:52px;font-family:"PT Serif",Georgia,serif;font-size:10px;color:var(--ink)}
.nav a{position:absolute;top:39px;font-size:9.5px;color:var(--ink);text-decoration:none;transform:translateX(-50%);white-space:nowrap}
.nav a.active{color:var(--accent)}
.nav-underline{left:527px;top:56px;width:70px;height:1px;background:var(--accent)}

.crumbs{position:absolute;left:0;top:86px;width:782px;height:35px;background:var(--bar);font-size:9px;color:#fff;padding:13px 0 0 64px}
.crumbs b{color:var(--accent)}

.section-title{left:0;width:782px;top:164px;text-align:center;font-size:16.5px;font-weight:700}
.intro{left:62px;width:658px;top:199px;text-align:center;font-size:9px;line-height:13.4px;color:var(--text)}

.tabs-line{left:72px;top:344px;width:638px;height:1px;background:var(--line)}
.tab-arrow{top:339px;width:10px;height:10px;border:1px solid var(--line);font-size:7px;color:#aaa;text-align:center;line-height:8px;background:#fff}
.tab-active{left:149px;top:343px;width:45px;height:1px;background:var(--accent)}
.tab-active-tip{left:167px;top:344px;width:0;height:0;border-left:4px solid transparent;border-right:4px solid transparent;border-top:4px solid var(--accent)}
.service-icon{top:269px;width:62px;height:62px;border:1px solid #333;border-radius:50%;display:flex;align-items:center;justify-content:center}
.service-icon.active{border-color:var(--accent)}
.service-label{top:356px;font-size:9px;color:var(--ink);transform:translateX(-50%);white-space:nowrap}
.service-label.active{color:var(--accent)}

.timeline{left:391px;top:412px;width:1px;height:398px;background:var(--line)}
.dot{width:8px;height:8px;border-radius:50%;background:#888;left:387px}
.dot-active{left:378px;top:433px;width:26px;height:26px;border:1px solid var(--accent);border-radius:50%;background:#fff}
.dot-active::after{content:"";position:absolute;left:5px;top:5px;width:14px;height:14px;border-radius:50%;background:var(--accent)}
.entry-title{right:423px;top:428px;text-align:right;font-size:16.5px;line-height:20px}
.entry-title strong{display:block}
.entry-text{left:38px;width:321px;top:483px;text-align:right;font-size:9px;line-height:13.4px;color:var(--text)}

.cta{position:absolute;left:0;top:835px;width:782px;height:183px;background:var(--band);text-align:center;color:#fff}
.cta h2{position:absolute;left:0;width:782px;top:50px;font-size:19.5px;letter-spacing:2.6px;font-weight:700}
.cta p{position:absolute;left:0;width:782px;top:78px;font-size:8.5px;letter-spacing:1.3px;font-weight:700}
.cta .button{position:absolute;left:338px;top:108px;width:106px;height:27px;border:1.5px solid #fff;border-radius:2px;font-size:9px;font-weight:700;line-height:24px}

.footer{position:absolute;left:0;top:1018px;width:782px;height:149px;background:var(--footer);color:#fff}
.footer h4{position:absolute;top:30px;font-size:9.5px;font-weight:400;letter-spacing:.3px}
.divider{top:26px;width:1px;height:102px;background:#3a3a3a}
.social{top:56px;width:46px;height:60px;text-align:center;font-size:8px}
.social i{display:block;width:24px;height:24px;border-radius:50%;background:rgba(255,255,255,.2);margin:9px auto 9px}
.footer .small{font-size:7px;color:#999;line-height:12px}
.email{left:349px;top:85px;width:130px;height:18px;background:#fff;font-size:6.5px;color:#aaa;padding:5px 10px}
.email-btn{left:478px;top:85px;width:21px;height:18px;background:var(--accent);display:flex;align-items:center;justify-content:center}
.menu{left:633px;top:56px;font-size:7.5px;line-height:14px;list-style:none}

.bottom{position:absolute;left:0;top:1167px;width:782px;height:33px;background:var(--bottom);text-align:center;font-size:7px;color:#777;line-height:33px}
</style>
</head>
<body>

<header class="header">
  <div class="abs brand">Halvik.</div>
  <div class="abs tagline">Leadership toolkit for firms on the rise</div>
  <nav class="nav">
    <a style="left:412px">Home</a>
    <a style="left:485px">About Us</a>
    <a class="active" style="left:558px">Services</a>
    <a style="left:632px">Gallery</a>
    <a style="left:702px">Contact Us</a>
  </nav>
  <div class="abs nav-underline"></div>
</header>

<div class="crumbs">Home &nbsp;&gt;&gt;&nbsp; <b>Services</b></div>

<h1 class="abs section-title">Our Services</h1>
<p class="abs intro">Donec eu viverra odio, eu cursus orci. Vestibulum id imperdiet est, non dictum leo. Aenean dictum nunc ex, quis vehicula dolor posuere id. Donec luctus luctus nisl, id porta turpis. Class aptent taciti sociosqu ad litora torquent per conubia nostra, per inceptos himenaeos. Curabitur metus libero, suscipit pretium erat sed, cursus faucibus erat. Vestibulum ante ipsum primis in</p>

<div class="abs tabs-line"></div>
<div class="abs tab-arrow" style="left:62px">‹</div>
<div class="abs tab-arrow" style="left:709px">›</div>

<div class="abs service-icon active" style="left:139px">
  <svg width="30" height="24" viewBox="0 0 30 24" fill="#e8992f"><rect x="2" y="10" width="4" height="10"/><rect x="8" y="14" width="4" height="6"/><rect x="14" y="6" width="4" height="14"/><rect x="20" y="12" width="4" height="8"/><rect x="26" y="4" width="3" height="16"/><rect x="0" y="21" width="30" height="2"/></svg>
</div>
<div class="abs service-icon" style="left:285px">
  <svg width="30" height="26" viewBox="0 0 30 26" fill="#2d3540"><path d="M2 9h6l14-8v22L8 15H2z"/><path d="M8 15l3 9h4l-2-9z"/><rect x="24" y="9" width="4" height="6" rx="1"/></svg>
</div>
<div class="abs service-icon" style="left:430px">
  <svg width="26" height="26" viewBox="0 0 26 26" fill="none" stroke="#2d3540" stroke-width="2"><rect x="2" y="4" width="22" height="20" rx="1"/><path d="M2 10h22M7 1v6M19 1v6M2 15h22M2 20h22M8 10v14M13 10v14M18 10v14"/></svg>
</div>
<div class="abs service-icon" style="left:581px">
  <svg width="32" height="26" viewBox="0 0 32 26" fill="none" stroke="#2d3540" stroke-width="2.2" stroke-linejoin="round"><rect x="1" y="11" width="6" height="13" fill="#2d3540"/><path d="M9 12l5-7c1-2 4-2 4 1l-1 4h11a2 2 0 010 4h-6M9 12v11h12a2 2 0 000-4h-1m1 4"/></svg>
</div>

<div class="abs tab-active"></div>
<div class="abs tab-active-tip"></div>

<div class="abs service-label active" style="left:172px">Growth Management</div>
<div class="abs service-label" style="left:317px">Corporate Communication</div>
<div class="abs service-label" style="left:462px">Project Management</div>
<div class="abs service-label" style="left:612px">Concepetualizing</div>

<div class="abs timeline"></div>
<div class="abs dot-active"></div>
<div class="abs dot" style="top:573px"></div>
<div class="abs dot" style="top:690px"></div>
<div class="abs dot" style="top:806px"></div>

<h2 class="abs entry-title" style="font-weight:400">Growth<strong>Management</strong></h2>
<p class="abs entry-text">Pellentesque feugiat lacus a leo faucibus facilisis. Sed non tristique massa. Integer molestie, nunc quis sollicitudin condimentum.Pellentesque feugiat lacus a leo faucibus facilisis. Sed non tristique massa. Integer molestie, nunc quis sollicitudin condimentum.</p>

<section class="cta">
  <h2>DONEC EU VIVERRA ODIO, EU CURSUS ORCI.</h2>
  <p>IN VARIUS VENENATIS ELIT, A PLACERAT LACUS. MAURIS SUSCIPIT</p>
  <div class="button">CONTACT NOW</div>
</section>

<footer class="footer">
  <h4 style="left:64px">Let’s Connect</h4>
  <div class="abs social" style="left:64px;background:var(--social-a)"><i></i>2598</div>
  <div class="abs social" style="left:116px;background:var(--social-b)"><i></i>4576</div>
  <div class="abs social" style="left:168px;background:var(--social-c)"><i></i>1269</div>

  <div class="abs divider" style="left:285px"></div>

  <h4 style="left:348px">Mailing List</h4>
  <p class="abs small" style="left:349px;top:52px">Sign up for our mailing list to get latest<br>updates and offers.</p>
  <div class="abs email">Email address</div>
  <div class="abs email-btn"><svg width="8" height="7" viewBox="0 0 8 7"><path d="M1 3.5l2 2L7 1" stroke="#fff" stroke-width="1.6" fill="none"/></svg></div>
  <p class="abs small" style="left:349px;top:107px;color:#777">We respect your privacy</p>

  <div class="abs divider" style="left:569px"></div>

  <h4 style="left:633px">Menu</h4>
  <ul class="abs menu">
    <li>Home</li><li>About Us</li><li>Services</li><li>Gallery</li><li>Contact Us</li>
  </ul>
</footer>

<div class="bottom">© Copyrights 2015 All Rights Reserved</div>

</body>
</html>
```